Create an awesome website for a medical clinic

This is a new website for a doctor's office. The site should be clean and modern, easy to navigate.

This is a wellness clinic, we want to help our clients have a healthy, active lifestyle. It should be friendly and inviting, and easy for them to call or schedule an appointment.

The site should be responsive and designed using the attached Bootstrap 3 PSD.

We will provide stock photos, until then please use stock photos from:

pixelharbor.com or
framequarry.com (preferred)

Some example sites of clean and modern designs that we like:

https://tulsaspinecare.com/
http://reachpastjoints.com/
http://turninghealthier.com/

Also attached is a temporary logo you can use.

Reason: Thank you everyone for your great designs - we need a little more time so I'm extending the project.

Need extra days to review

Also, the colors in the new logo I just linked to are the final colors of the logo, so feel free to use any complimentary colors to it.

Hi everyone, The boss wants to change the layout of the site a little bit - here's the revised layout: https://www.filecrate.com/s/k9rt31vx2qp84zn/notes%2011_29_2017.pdf?dl=0 And the graphic assets you can use are here: https://www.filecrate.com/s/k9rt31vx2qp84zn/notes%2011_29_2017.pdf?dl=0 Feel free to change the background color of the "topbar", and change the icons of the "why people trust us" if you want, these are just temporary placeholders. Thanks for your patience and hard work!

Target Market(s)

People seeking medical treatment (wellness clinic)

Industry/Entity Type

Doctor

Number of Pages Required

1 page

Font styles to use
Sans Serif

Colors
0592cd
33a6d7
abd037
9bcb3c

Requirements
Must have
• The home page should have: a strong hero image/slideshow, clinic phone number should be prominent and at the top of the page (in the nav), a "what to expect" section (this is like a FAQs section - see attachment), and a strong call to action (a button to call or schedule an appointment).
• The what to expect section is useful so that prospective clients can determine if we're a good fit for them or not. It's a basic, first-step pre-qualification block of information.
• Social media icons which links to our social media profiles should be included.
Nice to have
• - Link to 3 most recent blog entries
• - Testimonials
• - How a multilevel nav menu looks.

```html
<!DOCTYPE html>
<html lang="en">
<head>
<meta charset="utf-8">
<title>Fernwell Clinic</title>
<link href="https://fonts.googleapis.com/css2?family=Montserrat:wght@400;500&family=Open+Sans:wght@400;600;700&display=swap" rel="stylesheet">
<style>
:root{
  --blue:#0592cd;
  --blue-light:#33a6d7;
  --bar:#1f1f1f;
  --menu-line:#7a746d;
  --text:#3a3a3a;
  --white:#ffffff;
}
*{margin:0;padding:0;box-sizing:border-box}
html,body{width:1200px;height:1200px;overflow:hidden;background:var(--white)}
body{position:relative;font-family:"Open Sans",sans-serif;color:var(--text)}
.abs{position:absolute}

.topbar{left:75px;top:0;width:1050px;height:34px;background:var(--bar)}
.nav-item{top:0;height:34px;line-height:33px;color:var(--white);font-size:13px;font-weight:600;transform:translateX(-50%);white-space:nowrap}
.nav-sep{top:5px;width:1px;height:24px;background:#444}
.nav-active-line{left:841px;top:31px;width:106px;height:3px;background:var(--blue-light)}
.hamburger{left:1072px;top:9px;width:22px}
.hamburger span{display:block;height:3px;background:var(--white);margin-bottom:3px;border-radius:1px}

.submenu{background:rgba(80,76,70,.9);color:var(--white);font-size:11.5px;line-height:28px;text-align:center}
.submenu div{height:28px;border-bottom:1px solid var(--menu-line)}
.submenu div:last-child{border-bottom:none}

.hero{left:75px;top:34px;width:1050px;height:582px;
  background:
    radial-gradient(ellipse at 40% 50%, #d9a887 0%, rgba(217,168,135,0) 45%),
    radial-gradient(ellipse at 80% 20%, #f1ece6 0%, rgba(241,236,230,0) 40%),
    linear-gradient(180deg,#c9b7a4 0%,#d6b49a 45%,#e8dfd2 75%,#cfc3a4 100%)}
.caption{left:140px;top:376px;width:394px;height:182px;background:rgba(110,95,85,.78);color:var(--white);text-align:center;font-family:"Montserrat",sans-serif}
.caption h1{font-weight:400;font-size:27px;margin-top:10px;letter-spacing:.3px}
.caption .rule{width:186px;height:2px;background:var(--white);margin:6px auto 10px}
.caption p{font-size:18.5px;line-height:23px;text-align:left;padding:0 30px 0 33px}
.btn{left:138px;top:138px;width:117px;height:31px;border:2px solid var(--white);border-radius:5px;font-family:"Open Sans",sans-serif;font-weight:700;font-size:12px;line-height:27px}
.arrow{top:306px;width:32px;height:40px;background:rgba(80,80,80,.75)}
.dot{top:580px;width:11px;height:11px;border-radius:50%;border:1.5px solid var(--white)}

.brand-card{left:164px;top:0;width:212px;height:150px}
.phone{left:0;top:6px;width:212px;text-align:center;color:var(--blue);font-weight:700;font-size:17px;display:flex;justify-content:center;align-items:center;gap:6px}
.brand-rule{left:14px;top:35px;width:186px;height:3px;background:var(--blue)}
.brand-name{left:0;top:72px;width:212px;text-align:center;color:var(--text);font-weight:600;font-size:22px;line-height:1.2;letter-spacing:.5px}

.section-title{left:0;top:648px;width:1200px;text-align:center;color:var(--blue);font-size:30px;font-weight:400}
.section-rule{left:286px;top:692px;width:628px;height:3px;background:var(--blue)}

.photo{width:211px;height:223px}
.feature{width:204px;font-size:14.6px;line-height:17.3px}
.feature h2{color:var(--blue);font-weight:400;font-size:20px;line-height:23.5px;margin-bottom:12px;margin-top:2px}
.feature.left{text-align:right}
</style>
</head>
<body>

<div class="abs hero" role="img" aria-label="Hero slide: woman relaxing during a back massage at a spa table with candles and flowers"></div>

<div class="abs topbar"></div>
<div class="abs nav-item" style="left:451px">Home</div>
<div class="abs nav-sep" style="left:506px"></div>
<div class="abs nav-item" style="left:562px">What to Expect</div>
<div class="abs nav-sep" style="left:618px"></div>
<div class="abs nav-item" style="left:673px">About</div>
<div class="abs nav-sep" style="left:728px"></div>
<div class="abs nav-item" style="left:783px">Blog</div>
<div class="abs nav-sep" style="left:839px"></div>
<div class="abs nav-item" style="left:894px">Testimonials</div>
<div class="abs nav-sep" style="left:949px"></div>
<div class="abs nav-item" style="left:1004px">Contact</div>
<div class="abs nav-active-line"></div>
<div class="abs hamburger"><span></span><span></span><span></span></div>

<div class="abs submenu" style="left:841px;top:34px;width:106px">
  <div>Submenu 1</div>
  <div>Submenu 2 &nbsp;›</div>
  <div>Submenu 3</div>
</div>
<div class="abs submenu" style="left:950px;top:64px;width:106px">
  <div>Submenu 2.1</div>
  <div>Submenu 2.2</div>
  <div>Submenu 2.3</div>
</div>

<svg class="abs brand-card" viewBox="0 0 212 150" aria-hidden="true">
  <polygon points="0,0 212,0 212,150 106,136 0,150" fill="#fff"/>
</svg>
<div class="abs brand-card">
  <div class="abs phone">
    <svg width="20" height="16" viewBox="0 0 20 16" aria-hidden="true"><path d="M1 6 Q10 -1 19 6 L16 8 L14 5 Q10 3 6 5 L4 8 Z" fill="#0592cd"/><rect x="4" y="8" width="12" height="7" rx="2" fill="#0592cd"/><circle cx="10" cy="11.5" r="2" fill="#fff"/></svg>
    555 - 014 - 7720
  </div>
  <div class="abs brand-rule"></div>
  <div class="abs brand-name">Fernwell Clinic</div>
</div>

<div class="abs caption">
  <h1>Lorem Ipsum Dolor</h1>
  <div class="rule"></div>
  <p>Dictumst consectetuer donec mi, vestibulum commodo eget nec in at viverra sociis bibendum.</p>
  <div class="abs btn">SCHEDULE NOW</div>
</div>

<svg class="abs arrow" style="left:75px" viewBox="0 0 32 40" aria-hidden="true"><polyline points="20,8 9,20 20,32" fill="none" stroke="#fff" stroke-width="1.5"/></svg>
<svg class="abs arrow" style="left:1093px" viewBox="0 0 32 40" aria-hidden="true"><polyline points="12,8 23,20 12,32" fill="none" stroke="#fff" stroke-width="1.5"/></svg>
<div class="abs dot" style="left:575px;background:#fff"></div>
<div class="abs dot" style="left:595px"></div>
<div class="abs dot" style="left:615px"></div>

<div class="abs section-title">What to Expect</div>
<div class="abs section-rule"></div>

<div class="abs feature left" style="left:148px;top:732px">
  <h2>Headline 1<br>Example Text</h2>
  Lorem ipsum dolor sit amet, mus convallis turpis a, sed sollicitudin quisquam wisi lectus proin, primis integer sapien dolor, suspendisse nulla vestibulum sed nibh pharetra cursus, est sagittis dolor velit.
</div>
<div class="abs photo" style="left:377px;top:725px;background:linear-gradient(180deg,#9bb7dc 0%,#c9d6e6 30%,#8f9aa0 55%,#bfc4c2 80%,#a9b28a 100%)" role="img" aria-label="Modern clinic building exterior with palm trees and driveway"></div>
<div class="abs photo" style="left:612px;top:725px;background:linear-gradient(180deg,#e3e1dc 0%,#cfd3d6 50%,#9a6a45 80%,#7a4f33 100%)" role="img" aria-label="Receptionist greeting a senior patient at the front desk"></div>
<div class="abs feature" style="left:847px;top:732px">
  <h2>Headline 2<br>Example Text</h2>
  Aliquet nam feugiat, mattis ligula etiam. Sed ipsum luctus odio libero in. Turpis pede tortor. Libero in. Enim mauris elementum, tempus vehicula cras, sem sed nam scelerisque, metus lacus consequat, nec vitae amet.
</div>

<div class="abs feature left" style="left:148px;top:979px">
  <h2>Headline 3<br>Example Text</h2>
  Donvallis turpis a, sed sollicitudin quisquam wisi lectus proin, primis integer sapien dolor, suspendia vestibulum sed nibh pharetra cursus, est sagittis dolor velit, metus lacus consequat, nec vitae amet.
</div>
<div class="abs photo" style="left:377px;top:972px;background:linear-gradient(180deg,#f2f2f2 0%,#d9d6d0 40%,#a89f8e 70%,#c8c6c2 100%)" role="img" aria-label="Patients seated in a clinic waiting room"></div>
<div class="abs photo" style="left:612px;top:972px;background:linear-gradient(90deg,#f4f6f8 0%,#dbe9f2 50%,#c3dceb 75%,#eadbe2 100%)" role="img" aria-label="Doctor in white coat holding hands with an elderly patient"></div>
<div class="abs feature" style="left:847px;top:979px">
  <h2>Headline 4<br>Example Text</h2>
  In massa egestas justo libero, nulla auctor auctor suspendisse scelerisque nam ut, molestie lacinia non amet nulla. Aut nonummy eu fusce lorem, metus lacus consequat, nec vitae amet molestie nonummy.
</div>

</body>
</html>
```